Power Point Showing our WHY: R4V

Project Description:
This PowerPoint design project aims to humanize critical educational statistics by transforming data into a powerful visual narrative. The goal is to put a face to the data, making abstract percentages more tangible and emotionally resonant for audiences.

The presentation begins with a single, impactful visual: 100 K–12 students, diverse in race and ethnicity, representing the full spectrum of learners across America.

Slide Progression & Visual Design:
Slide 1: "The Starting Line – 100 Students"
A visual display of 100 illustrated or photographic K–12 students.
Representation includes diversity in race, ethnicity, gender, and clothing to reflect real classrooms.
This slide sets the stage: every student matters.
Slide 2: "The First Drop – High School Graduation"
20 students fade away, showing the stark reality that only 80% graduate from high school.
Remaining 80 students stay on screen, reinforcing the message: not all students make it to the finish line.
Slide 3: "College Completion – A Narrowing Path"
From the 80 remaining students, another 35 fade away, illustrating that only 56% of students earn a college degree.
This leaves 45 students visible, showing the significant drop-off even after high school graduation.
Slide 4: "Low-Income Learners – The Equity Gap"
The image resets to the original 100 students.
This time, 87 students fade away, leaving only 13 standing, representing the 13% of low-income students who earn a college degree.
The emotional impact is amplified by the dramatic reduction in students who overcome economic barriers.
Design Notes:
Use consistent character illustrations or silhouettes for cohesion.
Employ subtle animations for "fading out" to enhance storytelling.
Slides should have minimal text—statistics should be overlaid in bold, clean typography.
Backgrounds should remain neutral or slightly muted to keep the focus on the students.
I am including out template to use

```html
<!DOCTYPE html>
<html lang="en">
<head>
<meta charset="utf-8">
<title>R4V – Our Why</title>
<link rel="stylesheet" href="https://fonts.googleapis.com/css2?family=Poppins:wght@500;600&display=swap">
<style>
  :root{
    --page:#d4d4d4;
    --slide:#f9f9f9;
    --ink:#1d1d1d;
    --navy:#0b2e3d;
    --teal:#1f6f8b;
    --magenta:#b3155f;
    --white:#ffffff;
  }
  *{box-sizing:border-box;margin:0;padding:0}
  html,body{width:1200px;height:723px;overflow:hidden;background:var(--page)}
  body{position:relative;font-family:"Poppins",sans-serif;color:var(--ink)}
  .defs{position:absolute;width:0;height:0}
  .slide{position:absolute;width:549px;height:308px;background:var(--slide);overflow:hidden}
  .slide--1{left:34px;top:39px}
  .slide--2{left:610px;top:39px}
  .slide--3{left:35px;top:364px}
  .slide--4{left:611px;top:364px}
  .crowd{position:absolute;left:0;top:0;width:549px;height:308px}
  .tag{position:absolute;left:16px;top:14px;height:30px;border-radius:15px;background:var(--navy);
       color:var(--white);font-weight:600;font-size:14.5px;line-height:30px;text-align:center;white-space:nowrap}
  .slide--1 .tag{width:194px}
  .slide--2 .tag{left:18px;top:13px;width:337px;font-size:13.8px}
  .slide--3 .tag{left:18px;top:13px;width:337px;font-size:13.8px}
  .slide--4 .tag{left:18px;top:13px;width:264px;font-size:13.8px}
  .brand{position:absolute;right:24px;top:26px;display:flex;align-items:center;gap:8px;
         font-weight:600;font-size:32px;line-height:40px;color:var(--teal);letter-spacing:1px}
  .brand__dot{width:14px;height:14px;border-radius:50%;background:var(--magenta)}
  .title{position:absolute;font-weight:600;font-size:23.5px;line-height:27px;color:var(--ink);white-space:nowrap}
  .accent-teal{color:var(--teal)}
  .accent-magenta{color:var(--magenta)}
  .slide-number{position:absolute;right:15px;bottom:10px;width:36px;height:36px;border-radius:50%;
                background:var(--white);box-shadow:0 0 3px rgba(0,0,0,.15);color:var(--teal);
                font-weight:600;font-size:14px;line-height:36px;text-align:center}
</style>
</head>
<body>
<svg class="defs" aria-hidden="true">
  <defs>
    <linearGradient id="crowdTones" x1="0" y1="0" x2="1" y2="1">
      <stop offset="0" stop-color="#c9876f"/>
      <stop offset=".25" stop-color="#5f7696"/>
      <stop offset=".45" stop-color="#c8604a"/>
      <stop offset=".65" stop-color="#7e8ea6"/>
      <stop offset=".85" stop-color="#cf6a4f"/>
      <stop offset="1" stop-color="#d9c3a8"/>
    </linearGradient>
    <filter id="fadeBlur" x="-20%" y="-20%" width="140%" height="140%">
      <feGaussianBlur stdDeviation="7"/>
    </filter>
  </defs>
</svg>

<section class="slide slide--1">
  <svg class="crowd" viewBox="0 0 549 308" role="img" aria-label="Illustrated crowd of one hundred diverse students walking forward">
    <path d="M0 64 L112 63 Q150 80 180 107 Q250 150 307 190 Q360 225 404 253 Q450 285 482 308 L0 308 Z" fill="url(#crowdTones)"/>
  </svg>
  <div class="tag">Every Student Matters</div>
  <div class="brand"><span class="brand__dot"></span>R4V</div>
  <div class="title" style="left:331px;top:94px">The <span class="accent-teal">Starting</span> Line<br>100 Students</div>
  <div class="slide-number">01</div>
</section>

<section class="slide slide--2">
  <svg class="crowd" viewBox="0 0 549 308" role="img" aria-label="Illustrated crowd of students where the front fifth fades away, leaving eighty standing">
    <path d="M0 52 L112 54 Q170 80 220 115 Q255 135 281 151 L247 308 L0 308 Z" fill="url(#crowdTones)"/>
    <path d="M281 151 Q340 180 390 225 Q430 262 462 308 L247 308 Z" fill="url(#crowdTones)" opacity=".55" filter="url(#fadeBlur)"/>
  </svg>
  <div class="tag">Not All Students Make It To The Finish Line.</div>
  <div class="brand"><span class="brand__dot"></span>R4V</div>
  <div class="title" style="left:307px;top:81px">The <span class="accent-magenta">First Drop</span> High<br>School Graduation</div>
  <div class="slide-number">02</div>
</section>

<section class="slide slide--3">
  <svg class="crowd" viewBox="0 0 549 308" role="img" aria-label="Illustrated crowd of students with a central group blurred and fading away, leaving forty-five standing">
    <path d="M0 56 L112 55 Q150 72 180 99 Q250 142 307 182 Q360 220 404 250 Q450 283 482 308 L0 308 Z" fill="url(#crowdTones)"/>
    <circle cx="150" cy="201" r="84" fill="#ece8e6"/>
    <circle cx="150" cy="201" r="80" fill="url(#crowdTones)" opacity=".45" filter="url(#fadeBlur)"/>
  </svg>
  <div class="tag">56% Of Students Earn A College Degree.</div>
  <div class="brand"><span class="brand__dot"></span>R4V</div>
  <div class="title" style="left:308px;top:81px">College <span class="accent-teal">Completion</span><br>A Narrowing Path</div>
  <div class="slide-number">03</div>
</section>

<section class="slide slide--4">
  <svg class="crowd" viewBox="0 0 549 308" role="img" aria-label="Illustrated crowd of one hundred students reset to the starting line">
    <path d="M0 56 L112 55 Q150 72 180 99 Q250 142 307 182 Q360 220 404 250 Q450 283 482 308 L0 308 Z" fill="url(#crowdTones)"/>
  </svg>
  <div class="tag">13% Of Low-income Students</div>
  <div class="brand"><span class="brand__dot"></span>R4V</div>
  <div class="title" style="left:270px;top:81px">Low-<span class="accent-teal">Income Learners</span><br>The Equity Gap</div>
  <div class="slide-number">04</div>
</section>
</body>
</html>
```